International business needs business cards

Our company, DRV Ventures Inc. is in the business of supplying a range construction products with particular emphasis on CEMENT. We have developed our own brand - TORVAN SUPPLIES - with which to infiltrate the market. We are launching our brand of cement (TORVAN Type IS Cement) into the Caribbean which is unlike anything this market has ever seen. A monopoly has existed here for the past 60-odd years and the market has now opened to allow the importation of other brands and consumers are anxious and ready for change/improvement. We are very excited to be launching and want to make a great first impression. We will be conducting workshops and seminars (from government level to the hardware store owners) and we want our business card to give us the strong, confident introduction that we need.

Target Market(s)

construction; builders; engineers; home owners

Industry/Entity Type

Construction

Contact Information for Business Card

Marisol Depree
CEO
cell # 1 555 4180736
Ground floor,Lindell Plaza Suite 2734
George Town,Grand Cayman
Cayman Islands,KY1-4823
EMAIL: m.depree@drvventuresinc.example
web site drvventuresinc.example

COMPANY: skype info drv.ventures.example

second card
Yvette Brannock-Depree
CFO
CELL# 1 555 607 3941
George Town,Grand Cayman
Cayman Islands,KY1-4823
EMAIL: y.brannockdepree@drvventuresinc.example
website drvventuresinc.example

Requirements
Must have
• Business cards must display BOTH logos - DRV is the company and TORVAN is the brand.

```html
<!DOCTYPE html>
<html lang="en">
<head>
<meta charset="utf-8">
<title>DRV Ventures Inc. — Business Card</title>
<link href="https://fonts.googleapis.com/css2?family=Arimo:wght@400;700&display=swap" rel="stylesheet">
<style>
  :root {
    --bg: #ecebe8;
    --brand-red: #8c1b21;
    --brand-red-dark: #6e1318;
    --brand-red-light: #a3262d;
    --card-white: #ffffff;
    --text-grey: #555555;
    --text-dark: #222222;
  }
  * { box-sizing: border-box; margin: 0; padding: 0; }
  html, body { width: 1200px; height: 950px; overflow: hidden; }
  body {
    background: var(--bg);
    font-family: "Arimo", Arial, sans-serif;
    position: relative;
  }
  .card {
    position: absolute;
    left: 250px;
    width: 700px;
    height: 400px;
    box-shadow: 0 6px 18px rgba(0,0,0,0.18);
  }
  /* Brand side */
  .card--brand {
    top: 50px;
    background: linear-gradient(135deg, var(--brand-red-light) 0%, var(--brand-red) 50%, var(--brand-red-dark) 100%);
    color: #fff;
  }
  .brand-mark {
    position: absolute;
    left: 50%;
    top: 120px;
    transform: translateX(-50%);
    display: flex;
    align-items: center;
    gap: 14px;
  }
  .brand-mark__dot {
    width: 26px; height: 26px;
    border-radius: 50%;
    background: #fff;
  }
  .brand-mark__name {
    font-size: 46px;
    font-weight: 700;
    letter-spacing: 4px;
    color: #fff;
  }
  .brand-url {
    position: absolute;
    left: 0; right: 0;
    top: 262px;
    text-align: center;
    font-size: 16px;
    letter-spacing: 2.5px;
  }
  /* Contact side */
  .card--contact {
    top: 490px;
    background: var(--card-white);
  }
  .company-mark {
    position: absolute;
    right: 48px;
    top: 42px;
    display: flex;
    align-items: center;
    gap: 12px;
  }
  .company-mark__square {
    width: 52px; height: 52px;
    background: var(--brand-red);
  }
  .company-mark__name {
    font-size: 28px;
    font-weight: 700;
    color: var(--text-dark);
  }
  .accent-bar {
    position: absolute;
    left: 0;
    top: 150px;
    width: 12px;
    height: 50px;
    background: var(--brand-red);
  }
  .person {
    position: absolute;
    left: 42px;
    top: 148px;
  }
  .person__name {
    font-size: 26px;
    font-weight: 700;
    color: var(--brand-red);
  }
  .person__title {
    font-size: 16px;
    color: var(--text-dark);
    margin-top: 6px;
  }
  .contacts {
    position: absolute;
    right: 48px;
    top: 140px;
    list-style: none;
    text-align: right;
    font-size: 16px;
    color: var(--text-grey);
  }
  .contacts li {
    display: flex;
    justify-content: flex-end;
    align-items: center;
    gap: 10px;
    line-height: 26px;
  }
  .contacts svg { width: 16px; height: 16px; flex: none; }
  .address {
    position: absolute;
    left: 42px;
    bottom: 40px;
    font-style: normal;
    font-size: 17px;
    line-height: 24px;
    color: var(--text-grey);
  }
</style>
</head>
<body>

<section class="card card--brand" aria-label="Card front">
  <div class="brand-mark">
    <span class="brand-mark__dot"></span>
    <span class="brand-mark__name">TORVAN</span>
  </div>
  <p class="brand-url">www.drvventuresinc.example</p>
</section>

<section class="card card--contact" aria-label="Card back">
  <div class="company-mark">
    <span class="company-mark__square"></span>
    <span class="company-mark__name">DRV Ventures Inc.</span>
  </div>

  <span class="accent-bar"></span>
  <div class="person">
    <p class="person__name">Marisol Depree</p>
    <p class="person__title">CEO</p>
  </div>

  <ul class="contacts">
    <li>1 555 4180736
      <svg viewBox="0 0 16 16" aria-hidden="true"><rect x="4" y="1" width="8" height="14" rx="1.5" fill="none" stroke="#8c1b21" stroke-width="1.6"/><circle cx="8" cy="12.5" r="0.9" fill="#8c1b21"/></svg>
    </li>
    <li>m.depree@drvventuresinc.example
      <svg viewBox="0 0 16 16" aria-hidden="true"><rect x="1" y="3" width="14" height="10" rx="1" fill="#8c1b21"/><path d="M1.5 3.5 L8 9 L14.5 3.5" fill="none" stroke="#fff" stroke-width="1.2"/></svg>
    </li>
    <li>drvventuresinc.example
      <svg viewBox="0 0 16 16" aria-hidden="true"><circle cx="8" cy="8" r="7" fill="#8c1b21"/><ellipse cx="8" cy="8" rx="3" ry="7" fill="none" stroke="#fff" stroke-width="1"/><line x1="1" y1="8" x2="15" y2="8" stroke="#fff" stroke-width="1"/></svg>
    </li>
  </ul>

  <address class="address">
    Ground floor<br>
    Lindell Plaza Suite 2734<br>
    George Town,Grand Cayman<br>
    Cayman Islands,KY1-4823
  </address>
</section>

</body>
</html>
```